Clean Modern Skin Product branding/ label.

I need a label for a skincare line. The company is Dermaloft but product names will vary. A couple products to list are:
Sensitive Cleanser, Lumeno, Repair, Halo up, Mendora, Mendora Plus, Mendora Intense, Tavelo, Balance and Vivanto.

I would like the color scheme to be muted greens, grays, tourquise. The bottles are white, boston shaped with pumps, and ounces are 2, 4, 8, 16 ounces. When I choose the design, I can give you exact label sizes. Along with the ingredience already on the product label.

The look I desire is clean, minimal. A modern, organic look. Ideas that come to mind are a Veloraine,https://www.veloraine-example.com/product/2846/37204/3-step/step-2-exfoliate/clarifying-lotion-1 and the simplicity of Bo Tarn.

Both styles high light the name, in this case Dermaloft, and then the specific product.

My product is clean utilizing pure ingredients rather that a bunch fillers and binders. When I work with my clients I normally will say we need to "restore the balance" from over use of harsh products. That is why this lines works. It restores the skin to it's natural state. The process is simple, so I would like the label to reflect that simplicity.

Target Market(s)

Anyone with sensitive skin. So gender neutral

Industry/Entity Type

Skin Care Product

Font styles to use
Serif
Sans Serif
Decorative

Colors
acd037
33b8a4
fcfefd
85cae6
d3d3d3

Requirements
Must have
• Logo, name of product and color identity for cleanser, Active products, moisturizers
• I am thinking we could have one color for a cleanser and a space where I can put a sticker on which cleanser it is. Acne Cleasner, Sensitive Cleanser, and Cleanser.
Nice to have
• Not sure....suprise me. I would like the font to stay the same on the DERMALOFT, but you can change color, or color of leaf.
Should not have
• Too busy, too crowded or look like every other skincare line

```html
<!DOCTYPE html>
<html lang="en">
<head>
<meta charset="utf-8">
<title>Dermaloft – Balance &amp; Vivanto label</title>
<link rel="stylesheet" href="https://fonts.googleapis.com/css2?family=Rubik:wght@500;700&family=Roboto:wght@300&family=Open+Sans:wght@700&display=swap">
<style>
  :root {
    --backdrop: #d4f00c;
    --label: #fcfefd;
    --ink-gray: #4a4d50;
    --ink-dark: #222426;
    --turquoise: #5fe3c4;
    --rule: #a8ecd9;
  }
  * { margin: 0; padding: 0; box-sizing: border-box; }
  html, body {
    width: 1200px;
    height: 1200px;
    overflow: hidden;
    background: var(--backdrop);
  }
  .label {
    position: absolute;
    left: 130px;
    top: 61px;
    width: 940px;
    height: 1078px;
    background: var(--label);
    box-shadow: 0 6px 14px rgba(0, 0, 0, 0.28);
  }
  .tagline {
    position: absolute;
    top: 262px;
    left: 0;
    width: 100%;
    text-align: center;
    font-family: "Rubik", sans-serif;
    font-weight: 700;
    font-size: 35px;
    color: var(--turquoise);
  }
  .brand-name {
    position: absolute;
    top: 350px;
    left: 0;
    width: 100%;
    text-align: center;
    font-family: "Rubik", sans-serif;
    font-weight: 500;
    font-size: 130px;
    line-height: 1;
    letter-spacing: -2px;
    color: var(--ink-gray);
  }
  .product-line {
    position: absolute;
    top: 578px;
    left: 0;
    width: 100%;
    display: flex;
    justify-content: center;
    align-items: center;
    gap: 14px;
    font-family: "Roboto", sans-serif;
    font-weight: 300;
    font-size: 72px;
    color: var(--ink-dark);
  }
  .product-word {
    padding: 0 4px 6px;
    border-top: 2px solid var(--rule);
    border-bottom: 2px solid var(--rule);
    line-height: 1.05;
  }
  .ampersand {
    color: var(--turquoise);
    font-size: 78px;
  }
  .volume {
    position: absolute;
    left: 635px;
    top: 960px;
    font-family: "Open Sans", sans-serif;
    font-weight: 700;
    font-size: 34px;
    color: var(--ink-dark);
  }
</style>
</head>
<body>
  <main class="label">
    <p class="tagline">restore the balance</p>
    <h1 class="brand-name">Dermaloft</h1>
    <p class="product-line">
      <span class="product-word">Balance</span>
      <span class="ampersand">&amp;</span>
      <span class="product-word">Vivanto</span>
    </p>
    <p class="volume">16 oz.</p>
  </main>
</body>
</html>
```